Delivery Docket urgent plus require many other designs for more stationary after this.

We need a new delivery docket design urgently as the one we have needs updating and we have changed our company name. Please do not copy the one I have uploaded as we do not feel this looks professional enough. I uploaded it as a few designers requested to see what we are currently using thank you.
It is quite complex in that we need a range of information to be on the one docket.
We are a Transport Company based in Australia that has a wide variety of items that we deliver such as water, sand and gravels and heavy equipment transport.
We would prefer to keep this design to A5 size as we will get them made into books. We are looking for a modern professional look. Although it is only a delivery docket this is given to all our customers so needs to look impressive.

We need our new logo on the docket (WTR). There will also need to be areas for our address and contact numbers, email etc these will be supplied to the winning designer to make the final adjustments so for now just put something generic in these spaces.
Needs to have an area for customer details, purchase order number, date and docket number (docket number to be in red)
Needs a section where we can list the type of product / and or service that has been provided and the amount / qty usually 3 lines will be enough for this. Need area under this where the customer can sign name and print name to say that the goods / and or services have been received.

Also required somewhere on the docket are the words, Tax Invoice will be issued based on the information provided on this docket. Conditions on back of page

We then need a separate section on the same page which we will use internally that the staff member can tear off and hand into the office. On this section it needs to have area where the driver can list km at start of job and at end with space to calculate km travelled, details of fuel purchased eg amount and litres, vehicle that is being used. also need to log down wheel bearing temps.
prime mover needs spaces as follows
Steer axel FL____________ Steer axel FR _________ 1st drive axel L_______
1st drive axel R_________ 2nd drive axel L_______ 2nd drive axel R________

For the trailers need something similar x 2 as have 2 trailers
1st axel DS_________ 1st axel PS_________ 2nd axel DS__________
2nd axel PS_________ 3rd axel DS_________ 3rd axel PS__________

I have included a few examples of designs we have used in past and ones that we like so you can get an idea of the colours we prefer, I have included some of the designs we are currently receiving for our logo that I like so you can get idea again of colours we prefer. There is much more we need designed also such as time sheets, more delivery dockets and letter heads so there is a lot of more work available to the winning designer.

Thank you

Customers

Serif
Sans Serif

Designer to choose colors to be used in the design.

• Please don't copy old docket as we do not like it and nned new info on new design thank you

```html
<!DOCTYPE html>
<html lang="en">
<head>
<meta charset="utf-8">
<title>WTR Delivery Docket</title>
<link href="https://fonts.googleapis.com/css2?family=Poppins:wght@400;500;600;700&display=swap" rel="stylesheet">
<style>
:root{
  --outer:#3a3a3a;
  --page:#ffffff;
  --ink:#111111;
  --black:#000000;
  --red:#ee1c1c;
  --band:#666666;
  --panel:#f5f5f5;
  --panel-cool:#eef0f0;
  --label-grey:#8c8c8c;
  --line:#444444;
  --muted:#555555;
}
*{box-sizing:border-box;margin:0;padding:0}
html,body{width:1200px;height:847px;overflow:hidden;background:var(--outer)}
body{font-family:'Poppins',sans-serif;color:var(--ink)}
.docket{position:absolute;left:0;top:0;width:1400px;height:988px;transform:scale(0.857143);transform-origin:0 0;background:var(--outer)}
.sheet{position:absolute;left:18px;top:18px;width:1364px;height:950px;background:var(--page)}
.frame{position:absolute;left:36px;top:36px;width:1330px;height:916px;border:4px solid #2b2b2b}
.abs{position:absolute}
.header{left:53px;top:45px;width:756px;height:105px;background:var(--black);color:#fff}
.brand{left:0;top:0;width:240px;height:105px;background:linear-gradient(135deg,#2a2a2a,#0d0d0d 60%,#232323);display:flex;align-items:center;justify-content:center}
.brand-name{font-weight:700;font-size:58px;letter-spacing:4px;color:#d9d9d9}
.contact{top:0;height:105px;display:flex;flex-direction:column;align-items:center;font-size:11.5px;line-height:17px;text-align:center}
.contact svg{margin:8px 0 14px}
.divider{top:22px;width:1px;height:62px;background:#777}
.docket-no{left:817px;top:45px;width:300px;height:50px;background:var(--red);clip-path:polygon(0 0,276px 0,100% 100%,0 100%);color:#fff;font-size:15px;display:flex;align-items:center;padding-left:8px}
.docket-no b{font-weight:600;margin-right:5px}
.date-label{left:1114px;top:63px;font-size:11px;font-weight:500}
.date-boxes{left:1160px;top:57px;display:flex}
.date-boxes span{width:21.5px;height:20px;border:1px solid #999;margin-left:-1px;font-size:10px;color:#aaa;text-align:center;line-height:17px}
.po{left:817px;top:102px;width:526px;height:48px;background:var(--band);color:#fff;font-size:14px;font-weight:500;display:flex;align-items:center;padding-left:10px}
.tab{left:53px;top:163px;width:226px;height:33px;background:var(--black);color:#fff;font-weight:600;font-size:14px;letter-spacing:.8px;clip-path:polygon(0 0,200px 0,100% 100%,0 100%);padding:8px 0 0 8px}
.customer{left:53px;top:195px;width:1294px;height:130px;background:var(--panel)}
.field{font-size:15px;font-weight:500}
.rule{height:1px;background:var(--line)}
.products-head{left:53px;top:326px;width:1294px;height:32px;background:var(--band);color:#fff;font-size:14px;font-weight:500;letter-spacing:.4px}
.products{left:53px;top:358px;width:1294px;height:159px;background:var(--panel)}
.notice{left:53px;top:480px;width:1294px;text-align:center;font-size:14px}
.sign-row{left:53px;top:527px;width:1294px;height:73px;border:1.5px solid #aaa;background:#fff}
.sign-label{top:0;height:72px;background:var(--label-grey);color:#fff;font-size:13.5px;letter-spacing:.6px;line-height:21px;display:flex;align-items:center}
.cut{left:53px;top:605px;width:1294px;height:24px}
.office{left:53px;top:645px;width:1294px;height:112px;background:var(--panel)}
.office-title{font-size:18px;font-weight:500;letter-spacing:1px}
.small{font-size:12px}
.val{font-size:11px;color:var(--muted)}
.bearings{left:55px;top:766px;width:1292px;height:166px;background:var(--panel-cool)}
.bt{font-size:12px}
.box{width:19px;height:19px;border:2px solid #333}
</style>
</head>
<body>
<div class="docket">
  <div class="sheet"></div>
  <div class="frame"></div>

  <div class="abs header">
    <div class="abs brand" role="img" aria-label="WTR company name on dark textured panel"><span class="brand-name">WTR</span></div>
    <div class="abs contact" style="left:262px;width:200px">
      <svg width="32" height="32" viewBox="0 0 32 32"><circle cx="16" cy="16" r="14.5" fill="none" stroke="#fff" stroke-width="2"/><path d="M16 8a5 5 0 0 0-5 5c0 4 5 10 5 10s5-6 5-10a5 5 0 0 0-5-5z" fill="#fff"/><circle cx="16" cy="13" r="2" fill="#000"/></svg>
      <div>14 HARBOUR RD KELSO PARK<br>Q 4300, SYDNEY, AUSTRALIA</div>
    </div>
    <div class="abs divider" style="left:465px"></div>
    <div class="abs contact" style="left:483px;width:120px">
      <svg width="32" height="32" viewBox="0 0 32 32"><circle cx="16" cy="16" r="14.5" fill="none" stroke="#fff" stroke-width="2"/><path d="M11 9.5l3 0 1.3 3.4-1.8 1.3a8 8 0 0 0 4.3 4.3l1.3-1.8 3.4 1.3v3c0 .7-.6 1.2-1.3 1.1C15 21.6 10.4 17 9.9 10.8c-.1-.7.4-1.3 1.1-1.3z" fill="#fff"/></svg>
      <div style="margin-top:6px">0400 555 0101<br>0400 555 0102</div>
    </div>
    <div class="abs divider" style="left:606px"></div>
    <div class="abs contact" style="left:620px;width:140px">
      <svg width="32" height="32" viewBox="0 0 32 32"><circle cx="16" cy="16" r="14.5" fill="none" stroke="#fff" stroke-width="2"/><circle cx="16" cy="16" r="7" fill="#fff"/><path d="M9 16h14M16 9v14M16 9c-3 3-3 11 0 14M16 9c3 3 3 11 0 14" stroke="#000" stroke-width="1.2" fill="none"/></svg>
      <div style="margin-top:6px">INFO@WTRHAUL.COM.AU<br>WWW.WTRHAUL.COM.AU</div>
    </div>
  </div>

  <div class="abs docket-no"><b>DELIVERY DOCKET NO:</b> 20512</div>
  <div class="abs date-label">DATE:</div>
  <div class="abs date-boxes"><span>D</span><span>D</span><span>M</span><span>M</span><span>Y</span><span>Y</span><span>Y</span><span>Y</span></div>
  <div class="abs po">PURCHASE ORDER NO: 201234</div>

  <div class="abs tab">CUSTOMER DETAILS</div>
  <div class="abs customer"></div>
  <div class="abs field" style="left:67px;top:211px">Name</div>
  <div class="abs rule" style="left:120px;top:228px;width:587px"></div>
  <div class="abs field" style="left:718px;top:213px">Phone</div>
  <div class="abs rule" style="left:771px;top:228px;width:213px"></div>
  <div class="abs field" style="left:991px;top:213px">Email</div>
  <div class="abs rule" style="left:1033px;top:228px;width:305px"></div>
  <div class="abs field" style="left:67px;top:248px">Address</div>
  <div class="abs rule" style="left:137px;top:265px;width:1201px"></div>
  <div class="abs field" style="left:67px;top:286px">City</div>
  <div class="abs rule" style="left:105px;top:301px;width:506px"></div>
  <div class="abs field" style="left:624px;top:286px">State</div>
  <div class="abs rule" style="left:671px;top:301px;width:445px"></div>
  <div class="abs field" style="left:1135px;top:286px">Zip</div>
  <div class="abs rule" style="left:1166px;top:301px;width:172px"></div>

  <div class="abs products-head"><span class="abs" style="left:12px;top:6px">PRODUCT / SERVICES</span><span class="abs" style="left:1087px;top:6px">AMOUNT/ QTY</span></div>
  <div class="abs products"></div>
  <div class="abs rule" style="left:67px;top:389px;width:1271px;background:#555"></div>
  <div class="abs rule" style="left:67px;top:426px;width:1271px;background:#555"></div>
  <div class="abs rule" style="left:67px;top:462px;width:1271px;background:#555"></div>
  <div class="abs" style="left:1021px;top:358px;width:2px;height:104px;background:#888"></div>
  <div class="abs notice">*** Tax Invoice will be issued based on the information provided on this docket. Conditions on back of page ***</div>

  <div class="abs sign-row">
    <div class="abs sign-label" style="left:0;width:226px;justify-content:center;text-align:center">GOODS RECEIVED BY<br>(PRINT NAME)</div>
    <div class="abs sign-label" style="left:558px;width:155px;justify-content:center;text-align:center">CUSTOMER<br>SIGNATURE</div>
    <div class="abs sign-label" style="left:955px;width:117px;padding-left:21px">DATE OF<br>RECEIVING</div>
  </div>

  <svg class="abs cut" viewBox="0 0 1294 24">
    <line x1="0" y1="12" x2="1294" y2="12" stroke="#111" stroke-width="2" stroke-dasharray="7 6"/>
    <g font-family="Poppins,sans-serif" font-size="22" text-anchor="middle" fill="#111">
      <rect x="96" y="2" width="24" height="20" fill="#fff"/><text x="108" y="20">✂</text>
      <rect x="471" y="2" width="24" height="20" fill="#fff"/><text x="483" y="20">✂</text>
      <rect x="845" y="2" width="24" height="20" fill="#fff"/><text x="857" y="20">✂</text>
      <rect x="1220" y="2" width="24" height="20" fill="#fff"/><text x="1232" y="20">✂</text>
    </g>
  </svg>

  <div class="abs office"></div>
  <div class="abs rule" style="left:55px;top:671px;width:526px;background:#333"></div>
  <div class="abs office-title" style="left:597px;top:660px">FOR OFFICE USE ONLY</div>
  <div class="abs rule" style="left:818px;top:671px;width:525px;background:#333"></div>

  <div class="abs small" style="left:65px;top:717px">Starting Point(km)</div>
  <div class="abs val" style="left:199px;top:714px">27450</div>
  <div class="abs rule" style="left:187px;top:731px;width:61px"></div>
  <div class="abs small" style="left:270px;top:718px">Destination Point(km)</div>
  <div class="abs val" style="left:410px;top:714px">28190</div>
  <div class="abs rule" style="left:407px;top:732px;width:59px"></div>
  <div class="abs small" style="left:488px;top:718px">Distance Travelled(km)</div>
  <div class="abs val" style="left:650px;top:714px">840</div>
  <div class="abs rule" style="left:636px;top:732px;width:60px"></div>
  <div class="abs small" style="left:727px;top:718px">Fuel Used(Lt)</div>
  <div class="abs val" style="left:828px;top:714px">84</div>
  <div class="abs rule" style="left:818px;top:732px;width:60px"></div>
  <div class="abs small" style="left:890px;top:718px">Amount($)</div>
  <div class="abs val" style="left:969px;top:714px">2560.00</div>
  <div class="abs rule" style="left:962px;top:732px;width:60px"></div>
  <div class="abs small" style="left:1059px;top:718px">Vehhicle</div>
  <div class="abs val" style="left:1136px;top:714px">Heavy Hauler 14 wheel</div>
  <div class="abs rule" style="left:1118px;top:732px;width:212px"></div>

  <div class="abs bearings"></div>
  <div class="abs rule" style="left:55px;top:796px;width:530px;background:#777"></div>
  <div class="abs" style="left:594px;top:787px;font-size:13px;font-weight:600;letter-spacing:.8px">LOG DOWN WHEEL BEARING TEMPS</div>
  <div class="abs rule" style="left:862px;top:796px;width:485px;background:#777"></div>

  <div class="abs box" style="left:69px;top:814px"></div>
  <div class="abs bt" style="left:97px;top:817px;color:#333">Prime Movers</div>
  <div class="abs box" style="left:201px;top:814px"></div>
  <div class="abs bt" style="left:233px;top:817px;color:#333">Trailers</div>

  <div class="abs bt" style="left:67px;top:854px">Steer axel FL</div><div class="abs rule" style="left:153px;top:867px;width:79px"></div>
  <div class="abs bt" style="left:265px;top:854px">Steer axel FR</div><div class="abs rule" style="left:353px;top:867px;width:79px"></div>
  <div class="abs bt" style="left:469px;top:854px">1st drive axel L</div><div class="abs rule" style="left:572px;top:867px;width:79px"></div>
  <div class="abs bt" style="left:764px;top:854px">1st axel DS</div><div class="abs rule" style="left:842px;top:867px;width:80px"></div>
  <div class="abs bt" style="left:962px;top:854px">1st axel PS</div><div class="abs rule" style="left:1043px;top:867px;width:79px"></div>
  <div class="abs bt" style="left:1166px;top:854px">2nd axel DS</div><div class="abs rule" style="left:1248px;top:867px;width:79px"></div>

  <div class="abs bt" style="left:67px;top:897px">1st drive axel R</div><div class="abs rule" style="left:167px;top:910px;width:79px"></div>
  <div class="abs bt" style="left:265px;top:897px">2nd drive axel L</div><div class="abs rule" style="left:372px;top:910px;width:79px"></div>
  <div class="abs bt" style="left:469px;top:897px">2nd drive axel R</div><div class="abs rule" style="left:577px;top:910px;width:79px"></div>
  <div class="abs bt" style="left:764px;top:897px">2nd axel PS</div><div class="abs rule" style="left:842px;top:910px;width:80px"></div>
  <div class="abs bt" style="left:962px;top:897px">3rd axel DS</div><div class="abs rule" style="left:1043px;top:910px;width:79px"></div>
  <div class="abs bt" style="left:1166px;top:897px">3rd axel PS</div><div class="abs rule" style="left:1248px;top:910px;width:79px"></div>
</div>
</body>
</html>
```